Brookvane Consulting Business Card Design

Business Card Design for Brookvane Consulting. Brookvane Consulting is a boutique consultancy based in Atlanta, GA., that specializes in marketing strategy, organization planning, and leadership development. We provide solutions for small businesses and startups as well as Vantage 300 companies.

http://brookvaneconsulting.com/

Target Market(s)

We provide solutions for small businesses and startups as well as Vantage 300 companies.

Industry/Entity Type

Consulting

Contact Information for Business Card

Two sided business card with priority on contact information, logo, tag line (Clear Plans, Steady Growth, Lasting Results)

Colors

Designer to choose colors to be used in the design.

Requirements
Must have
• contact information, logo, tag line (Clear Plans, Steady Growth, Lasting Results)
• Simple no over communication.
Nice to have
• I would like to see different placements of logo and creative use of both sides of the card
Should not have
• Do not put too much information on the card.

```html
<!DOCTYPE html>
<html lang="en">
<head>
<meta charset="utf-8">
<title>Brookvane Consulting Business Card</title>
<link rel="stylesheet" href="https://fonts.googleapis.com/css2?family=Roboto:wght@400;500&family=Pacifico&display=swap">
<style>
  :root {
    --backdrop: #1c1c1c;
    --card: #333333;
    --card-edge: #2a2a2a;
    --ink: #ffffff;
    --ink-soft: #bdbdbd;
  }
  * { box-sizing: border-box; margin: 0; padding: 0; }
  html, body { width: 799px; height: 1200px; overflow: hidden; }
  body {
    background: var(--backdrop);
    font-family: "Roboto", sans-serif;
    color: var(--ink);
    position: relative;
  }
  .card {
    position: absolute;
    left: 80px;
    width: 640px;
    height: 366px;
    background: var(--card);
    border: 1px solid var(--card-edge);
    border-radius: 26px;
    box-shadow: 0 12px 30px rgba(0,0,0,0.45);
  }
  .card--front { top: 110px; }
  .card--back { top: 720px; }

  .brand {
    display: flex;
    align-items: center;
    gap: 12px;
  }
  .brand__mark {
    width: 18px;
    height: 18px;
    background: var(--ink-soft);
    flex: none;
  }
  .brand__name {
    font-family: "Roboto", sans-serif;
    font-weight: 500;
    color: var(--ink-soft);
    letter-spacing: 0.5px;
    white-space: nowrap;
  }
  .card--front .brand {
    position: absolute;
    left: 50%;
    top: 50%;
    transform: translate(-50%, -50%);
  }
  .card--front .brand__name { font-size: 40px; }
  .card--front .brand__mark { width: 26px; height: 26px; }

  .holder {
    position: absolute;
    left: 58px;
    top: 54px;
    font-family: "Pacifico", cursive;
    font-size: 22px;
    color: var(--ink);
  }
  .contact {
    position: absolute;
    left: 58px;
    bottom: 56px;
    list-style: none;
    font-size: 15px;
    line-height: 1.45;
    color: var(--ink);
  }
  .back-brand {
    position: absolute;
    right: 46px;
    top: 140px;
  }
  .back-brand .brand__name { font-size: 26px; color: var(--ink); }
  .back-brand .brand__mark { background: var(--ink); width: 16px; height: 16px; }
  .tagline {
    margin-top: 8px;
    font-size: 10.5px;
    color: var(--ink-soft);
    letter-spacing: 0.3px;
    white-space: nowrap;
  }
</style>
</head>
<body>
  <section class="card card--front" aria-label="Card front">
    <div class="brand">
      <span class="brand__mark"></span>
      <span class="brand__name">Brookvane Consulting</span>
    </div>
  </section>

  <section class="card card--back" aria-label="Card back">
    <p class="holder">Tobias</p>
    <ul class="contact">
      <li>404-555-0142</li>
      <li>tobias@brookvaneconsulting.com</li>
      <li>www.brookvaneconsulting.com</li>
    </ul>
    <div class="back-brand">
      <div class="brand">
        <span class="brand__mark"></span>
        <span class="brand__name">Brookvane Consulting</span>
      </div>
      <p class="tagline">Clear Plans, Steady Growth, Lasting Results</p>
    </div>
  </section>
</body>
</html>
```